Gestaltung Mini Katalog für bayerische Polomarke
Gestaltung "Mini" Katalog für bayerische Polomarke
Zielgruppe
Unsere Marke richtet sich an den klassischen Lifestyle Kunden. 20 - 45 Jahre alt, legt Wert auf das Äussere und Kleidung.... Mag es gerne besonders, modern und chic.
Hallo,
wir planen derzeit einen kleinen Katalog von 8-10 Seiten im Format DIN A5 (kein Muss). Präsentiert wird darin die erste bayerische Polomarke K&M reitmode und die aktuellen Kollektionen an Polo-Teamshirts.
Die Fotos dazu werden in den nächsten 14 Tagen entstehen.
Wir suchen nun jemanden, der uns das ganze in eine moderne Gestaltung bringt. Für Vorschläge bitte statt der Fotos alternative Fotos einsetzen.
Unsere Marke bewegt sich im mittleren Preissegment und präsentiert eine ganz besondere Sportart. All das muss in dem Katalog rüber kommen. Neben den Produkt- und Modefotos werden klassische Polobilder integriert, um das Gefühl diesen Sports mit zu vermitteln.
Die Grundfarben sollten sich an denen von K&M reitmode orientieren: schwarz, blau, weiss.... Wobei wir für andere Farben, wenn diese passen bzw. begründet sind auch interessiert sind.

```html
<!DOCTYPE html>
<html lang="de">
<head>
<meta charset="utf-8">
<title>K&amp;M reitmode – Katalog 2009</title>
<link rel="stylesheet" href="https://fonts.googleapis.com/css2?family=Source+Sans+3:wght@400&display=swap">
<style>
  :root {
    --night: #000000;
    --polo-blue: #4aa6da;
    --ring-blue: #3f9fd6;
    --paper: #ffffff;
  }
  html, body {
    margin: 0;
    padding: 0;
    width: 1200px;
    height: 1200px;
    overflow: hidden;
    background: var(--night);
  }
  .catalog-cover {
    position: relative;
    width: 1200px;
    height: 1200px;
    background: var(--night);
    font-family: "Source Sans 3", "Helvetica Neue", Arial, sans-serif;
    color: var(--paper);
  }
  .cover-circles {
    position: absolute;
    top: 0;
    left: 0;
    width: 1200px;
    height: 936px;
    display: block;
  }
  .brand-block {
    position: absolute;
    top: 418px;
    left: 0;
    width: 1200px;
    text-align: center;
    color: var(--paper);
    font-weight: 400;
  }
  .brand-initials {
    display: block;
    font-size: 112px;
    line-height: 120px;
    letter-spacing: 4px;
  }
  .brand-word {
    display: block;
    margin-top: 20px;
    font-size: 36px;
    line-height: 40px;
    letter-spacing: 1px;
  }
  .cover-band {
    position: absolute;
    left: 0;
    top: 936px;
    width: 1200px;
    height: 264px;
    background: var(--polo-blue);
    display: flex;
    align-items: center;
    justify-content: center;
  }
  .cover-title {
    margin: 0;
    font-size: 44px;
    font-weight: 400;
    letter-spacing: 1px;
    color: var(--paper);
  }
</style>
</head>
<body>
  <main class="catalog-cover">
    <svg class="cover-circles" viewBox="0 0 1200 936" xmlns="http://www.w3.org/2000/svg" aria-hidden="true">
      <defs>
        <radialGradient id="ring-main" cx="0.5" cy="0.5" r="0.5" fx="0.38" fy="0.22">
          <stop offset="0" stop-color="var(--ring-blue)" stop-opacity="0"/>
          <stop offset="0.55" stop-color="var(--ring-blue)" stop-opacity="0.12"/>
          <stop offset="0.85" stop-color="var(--ring-blue)" stop-opacity="0.5"/>
          <stop offset="1" stop-color="var(--ring-blue)" stop-opacity="0.9"/>
        </radialGradient>
        <radialGradient id="ring-faint" cx="0.5" cy="0.5" r="0.5" fx="0.5" fy="0.7">
          <stop offset="0" stop-color="var(--ring-blue)" stop-opacity="0"/>
          <stop offset="0.7" stop-color="var(--ring-blue)" stop-opacity="0.04"/>
          <stop offset="1" stop-color="var(--ring-blue)" stop-opacity="0.3"/>
        </radialGradient>
      </defs>
      <rect class="cover-ground" width="1200" height="936" fill="var(--night)"/>
      <g style="mix-blend-mode: screen">
        <circle class="circle-lower-left" cx="560" cy="800" r="500" fill="url(#ring-faint)"/>
        <circle class="circle-lower-right" cx="920" cy="960" r="620" fill="url(#ring-faint)"/>
        <circle class="circle-top-main" cx="696" cy="180" r="540" fill="url(#ring-main)"/>
      </g>
    </svg>

    <p class="brand-block">
      <span class="brand-initials">K&amp;M</span>
      <span class="brand-word">reitmode</span>
    </p>

    <footer class="cover-band">
      <h1 class="cover-title">Katalog 2009</h1>
    </footer>
  </main>
</body>
</html>
```